I would like a business card to match my truck wrap and logo. I would like the font to match my existing business card please.

Industry/Entity Type

Painter

Contact Information for Business Card

Rodrigo Fenwar 801-437-2190 Fenwarcoatings.utah@brelmox.com
SERVICES - Custom Paint & Stain, Interior & Exterior, Epoxy Coatings / Garage Floors, Cabinet Refinishing, Log Staining and Refinishing.

Requirements
Nice to have
• I would like to have the white and grey line like the bottom of my vehicle wrap, Light Grey to match my truck also.

```html
<!DOCTYPE html>
<html lang="en">
<head>
<meta charset="utf-8">
<title>Fenwar Painting – Business Card</title>
<link href="https://fonts.googleapis.com/css2?family=Montserrat:wght@400;500;700&display=swap" rel="stylesheet">
<style>
  :root {
    --page-bg: #2a2a2c;
    --card-bg: #1e1e20;
    --brand-blue: #14a8e6;
    --text-light: #f2f2f2;
  }
  * { box-sizing: border-box; margin: 0; padding: 0; }
  html, body {
    width: 1200px; height: 900px; overflow: hidden;
    background: var(--page-bg);
    font-family: "Montserrat", sans-serif;
    color: var(--text-light);
  }
  .card {
    position: absolute;
    left: 170px;
    width: 860px;
    height: 400px;
    background: var(--card-bg);
    border-bottom: 6px solid var(--brand-blue);
    box-shadow: 0 10px 30px rgba(0,0,0,.5);
  }
  .card--front { top: 35px; }
  .card--back  { top: 465px; }

  .brand { display: flex; align-items: center; gap: 14px; }
  .brand__square { width: 46px; height: 46px; background: var(--brand-blue); }
  .brand__name {
    font-weight: 700; color: var(--brand-blue);
    font-size: 34px; line-height: 1.05; letter-spacing: 2px;
    text-transform: uppercase;
  }
  .brand__name span { display: block; font-size: 20px; letter-spacing: 10px; }

  .card--front .brand { position: absolute; top: 90px; left: 50%; transform: translateX(-50%); }
  .services { position: absolute; top: 235px; left: 0; right: 0; text-align: center; }
  .services__title {
    color: var(--brand-blue); font-weight: 500; font-size: 22px;
    letter-spacing: 2px; margin-bottom: 8px;
  }
  .services__list { font-size: 18px; line-height: 1.5; }
  .services__list .sep { color: var(--brand-blue); margin: 0 4px; }

  .card--back .brand { position: absolute; top: 150px; left: 60px; }
  .divider {
    position: absolute; left: 430px; top: 90px;
    width: 2px; height: 190px; background: var(--brand-blue);
  }
  .person { position: absolute; left: 470px; top: 95px; }
  .person__name {
    color: var(--brand-blue); font-weight: 500; font-size: 32px;
    letter-spacing: 1px; text-transform: uppercase;
  }
  .person__role { font-size: 20px; margin: 2px 0 20px; }
  .contact { list-style: none; font-size: 20px; line-height: 1.55; }
  .contact li { display: flex; align-items: center; gap: 10px; }
  .contact svg { width: 14px; height: 14px; flex: none; }
</style>
</head>
<body>
  <section class="card card--front">
    <div class="brand">
      <div class="brand__square"></div>
      <div class="brand__name">Fenwar<span>Painting</span></div>
    </div>
    <div class="services">
      <p class="services__title">SERVICES</p>
      <p class="services__list">Custom Paint &amp; Stain<span class="sep">|</span>Interior &amp; Exterior<span class="sep">|</span>Epoxy Coatings / Garage Floors</p>
      <p class="services__list">Cabinet Refinishing<span class="sep">|</span>Log Staining and Refinishing.</p>
    </div>
  </section>

  <section class="card card--back">
    <div class="brand">
      <div class="brand__square"></div>
      <div class="brand__name">Fenwar<span>Painting</span></div>
    </div>
    <div class="divider"></div>
    <div class="person">
      <p class="person__name">Rodrigo Fenwar</p>
      <p class="person__role">Director</p>
      <ul class="contact">
        <li>
          <svg viewBox="0 0 16 16" fill="var(--brand-blue)"><path d="M3 1l3 0 1 4-2 1a9 9 0 0 0 5 5l1-2 4 1v3c0 1-1 2-2 2A13 13 0 0 1 1 3c0-1 1-2 2-2z"/></svg>
          801-437-2190
        </li>
        <li>
          <svg viewBox="0 0 16 16" fill="none" stroke="var(--brand-blue)" stroke-width="1.5"><rect x="1" y="3" width="14" height="10"/><path d="M1 3l7 6 7-6"/></svg>
          Fenwarcoatings.utah@brelmox.com
        </li>
        <li>
          <svg viewBox="0 0 16 16" fill="none" stroke="var(--brand-blue)" stroke-width="1.3"><circle cx="8" cy="8" r="7"/><ellipse cx="8" cy="8" rx="3" ry="7"/><path d="M1 8h14"/></svg>
          www.fenwarcoatings-utah.com
        </li>
      </ul>
    </div>
  </section>
</body>
</html>
```